Theatrical Producer/Consultant needs Artistic Brochure Shell and Inserts

Lanternfield Stageworks (www.lanternfieldstageworks.com) is a small company that offers theatrical producing and consulting services. We would like to create a brochure that contains information about our various productions and services. Because our roster is fluid, we are proposing to create a brochure shell or folder with pockets, and then a template for individual tear sheets that would be inserted into the inside pockets of the brochure shell/folder. The shell is intended for reuse each season, and new tear sheets will be developed separately on a project by project basis.
This task is to create the shell and a corresponding tear sheet template.
The brochure will be delivered by hand as well as by mail, so should fit into a standard size mailing envelope (i.e., within NPDS flat dimensions of 6 1/8" x 11 1/2")
The final design should reflect the high level of artistry of our theatrical projects. Attached are our logo as well as photos of current theatrical offerings which are available for use on the brochure shell but not required. There is also a file that describes our services in more detail, fyi. This will ultimately go onto one of the tear sheets in the brochure.
For the tear sheet template, we have also included a sample brochure from a peer colleague, just to give you an idea of the kind of information each sheet would contain. Each project page will contain title of the project, information about the artists involved, one or more photos, a project description, schedule, fee and other technical information.
The final files for both the shell and tear sheet templates should be printer-ready and also in a file format that we can edit ourselves in future.
Updates
Project Deadline Extended Reason: There was a discrepancy between posted project deadline (December 7) and when project was automatically closed (December 6). Since several designers who have not yet submitted indicated they were planning to submit designs, we wanted to make sure that they were able to do so. Added Monday, December 7, 2015
Industry/Entity Type
Performing Art
Font styles to use
Look and feel
Each slider illustrates characteristics of the customer's brand and the style your logo design should communicate.

```html
<!DOCTYPE html>
<html lang="en">
<head>
<meta charset="utf-8">
<title>Lanternfield Stageworks – New Productions Sheets</title>
<link href="https://fonts.googleapis.com/css2?family=Lato:wght@300;400;700&display=swap" rel="stylesheet">
<style>
:root{
  --bg:#e8ebed;
  --paper:#ffffff;
  --teal:#1596ad;
  --teal-deep:#0f7d93;
  --mist:#cfe5eb;
  --mist-soft:#e6f2f5;
  --ink:#2d3a40;
  --ink-soft:#56656b;
  --rule:#5a676c;
}
*{box-sizing:border-box;margin:0;padding:0}
html,body{width:1200px;height:899px;overflow:hidden}
body{background:var(--bg);font-family:"Lato",sans-serif;color:var(--ink);position:relative}
.sheet-grid{display:grid;grid-template-columns:600px 600px;grid-template-rows:449.5px 449.5px;width:1200px;height:899px}
.cell{position:relative}
.page{position:absolute;left:150px;top:14px;width:300px;height:421px;background:var(--paper);overflow:hidden;box-shadow:0 2px 8px rgba(0,0,0,.18)}
.photo{position:absolute;border-radius:50%;background:radial-gradient(circle at 50% 60%,#c8453a 0 18%,#8a2a24 35%,#c79a5c 60%,#5a3320 100%);border:3px solid #fff}
.title{position:absolute;font-weight:300;font-size:25px;color:var(--ink);line-height:1}
.subtitle{position:absolute;font-size:6.5px;color:var(--ink)}
.credits{position:absolute;font-size:7.5px;line-height:1.25;color:var(--ink)}
.credits dt{font-size:5px;font-weight:700;margin-top:4px}
.credits dd{border-bottom:.6px solid var(--rule);padding-bottom:2px}
.checks{position:absolute;font-size:7px;color:var(--ink-soft);list-style:none;line-height:1.6}
.checks li::before{content:"☑ ";}
.body-copy{position:absolute;font-size:6.4px;line-height:1.45;color:var(--ink-soft);text-align:justify}
.dates-head{position:absolute;font-size:9px;font-weight:300;color:var(--ink)}
.dates{position:absolute;font-size:6px;line-height:1.45;color:var(--ink-soft);border-left:.8px solid var(--ink);padding-left:6px;list-style:none}
.footer-mark{position:absolute;bottom:8px;font-size:4.5px;letter-spacing:.3px;color:var(--ink-soft)}

/* cover */
.cover{background:linear-gradient(180deg,#fff 0%,#fff 22%,#bfe2ea 45%,var(--teal) 78%,var(--teal-deep) 100%)}
.cover .headline{position:absolute;left:60px;top:22px;font-weight:300;font-size:28px;line-height:.95;color:var(--ink)}
.cover .pattern-area{position:absolute;left:30px;top:70px;width:250px;height:210px;border-radius:50%;background:radial-gradient(ellipse at 45% 50%,rgba(255,255,255,.35) 0%,rgba(21,150,173,.18) 55%,rgba(21,150,173,0) 75%)}
.cover h2{position:absolute;left:22px;top:300px;font-size:11.5px;font-weight:400;color:#fff}
.cover .lede{position:absolute;left:22px;top:318px;width:256px;font-size:7px;line-height:1.45;color:#eaf7fa}

/* detail variants */
.detail-a{background:linear-gradient(180deg,#fff 0%,#fff 45%,var(--mist) 70%,#a9d3dd 100%)}
.detail-a .topline{position:absolute;left:12px;right:12px;top:58px;border-top:.8px solid var(--rule)}
.detail-a .band{position:absolute;left:0;right:0;top:222px;height:58px;background:#a9d6e0}
.detail-b{background:linear-gradient(180deg,#fff 0%,#fff 35%,var(--mist) 75%,#a9d3dd 100%)}
.detail-b .sidebar{position:absolute;left:0;top:0;width:128px;height:100%;background:linear-gradient(180deg,#c8e3ea,var(--mist-soft) 60%,#cfe5eb)}
.detail-c{background:linear-gradient(180deg,#fff 0%,#fff 40%,var(--mist-soft) 70%,#b7dbe3 100%)}
.detail-c .topline{position:absolute;left:150px;right:14px;top:58px;border-top:.8px solid var(--rule)}
</style>
</head>
<body>
<main class="sheet-grid">

  <section class="cell">
    <article class="page cover">
      <div class="headline">new<br>&nbsp;productions</div>
      <div class="pattern-area" role="img" aria-label="Decorative pattern in soft teal tones around the photo"></div>
      <div class="photo" role="img" aria-label="Photo of a performer in red on a stage in an ornate theatre" style="left:58px;top:95px;width:132px;height:132px"></div>
      <h2>Claritas est etiam processus dynamicus</h2>
      <p class="lede">Lorem ipsum dolor sit amet, consectetuer adipiscing elit, sed diam nonummy nibh euismod tincidunt ut laoreet dolore magna aliquam erat volutpat. Ut wisi enim ad minim veniam, quis nostrud exerci tation ullamcorper suscipit lobortis nisl ut aliquip ex ea commodo consequat.</p>
    </article>
  </section>

  <section class="cell">
    <article class="page detail-a">
      <div class="title" style="right:14px;top:18px">Act Name</div>
      <div class="subtitle" style="right:14px;top:46px">Based on the Act Name</div>
      <div class="topline"></div>
      <div class="photo" role="img" aria-label="Photo of a performer in red on a stage in an ornate theatre" style="left:20px;top:72px;width:102px;height:102px"></div>
      <dl class="credits" style="left:150px;top:64px;width:136px">
        <dt>Text By</dt><dd>Paul Brennan, Jean-Luc Corvalan<br>and Marie-Claire Estoril</dd>
        <dt>Directed by</dt><dd>Paul Brennan &amp; Marie-Claire Estoril</dd>
        <dt>Music</dt><dd>Tomo Sakurai</dd>
        <dt>Lighting</dt><dd>Philippe Varenne</dd>
        <dt>With</dt><dd style="border:0">Carine Kamanzi,<br>Jared Milburn, Eli Nzeyimana<br>and Sean O'Kearney</dd>
      </dl>
      <ul class="checks" style="left:20px;top:188px"><li>Show performed in English</li><li>Duration : 1h30 (tbc)</li></ul>
      <div class="band"></div>
      <p class="body-copy" style="left:20px;top:228px;width:262px">Lorem ipsum dolor sit amet, consectetuer adipiscing elit, sed diam nonummy nibh euismod tincidunt ut laoreet dolore magna aliquam erat volutpat. Ut wisi enim ad minim veniam, quis nostrud exerci tation ullamcorper suscipit lobortis nisl ut aliquip ex ea commodo consequat. Duis autem vel eum iriure dolor in hendrerit in vulputate velit esse molestie consequat.</p>
      <div class="dates-head" style="left:26px;top:290px">Performance Dates</div>
      <ul class="dates" style="left:30px;top:306px">
        <li>Sept. 15 to Oct. 17, 2015 Théâtre des Lanternes du Nord</li>
        <li>Nov. 17 to 21, 2015 Harbourlight Repertory Theatre/Singapore</li>
        <li>Nov. 25 to 29, 2015 Kestrel Theatre/Tokyo/Japan</li>
        <li>Dec. 10 to 11, 2015 Maison des Arts d'Aubrac</li>
        <li>Feb. 3 to 27, 2016 Old Quay Theatre/London/Great Britain</li>
        <li>March 5 to 12, 2016 Mumbai/India</li>
        <li>March 16 to 20, 2016 Pearl River Arts Festival</li>
        <li>May 11 to 15, 2016 Teatro Alcione/Rome/Italia</li>
      </ul>
      <div class="footer-mark" style="right:14px">NEW PRODUCTION 2015/2016</div>
    </article>
  </section>

  <section class="cell">
    <article class="page detail-b">
      <div class="sidebar"></div>
      <div class="photo" role="img" aria-label="Photo of a performer in red on a stage in an ornate theatre" style="left:12px;top:12px;width:104px;height:104px"></div>
      <div class="title" style="right:14px;top:16px">Act Name</div>
      <div class="subtitle" style="right:14px;top:44px">Based on the Act Name</div>
      <dl class="credits" style="left:10px;top:128px;width:112px;font-size:7px">
        <dt>Text By</dt><dd>Paul Brennan, Jean-Luc Corvalan and Marie-Claire Estoril</dd>
        <dt>Directed by</dt><dd>Paul Brennan &amp; Marie-Claire Estoril</dd>
        <dt>Music</dt><dd>Tomo Sakurai</dd>
        <dt>Lighting</dt><dd>Philippe Varenne</dd>
        <dt>With</dt><dd style="border:0">Carine Kamanzi,<br>Jared Milburn, Eli Nzeyimana<br>and Sean O'Kearney</dd>
      </dl>
      <ul class="checks" style="left:14px;top:290px"><li>Show performed in English</li><li>Duration : 1h30 (tbc)</li></ul>
      <p class="body-copy" style="left:140px;top:62px;width:146px">Lorem ipsum dolor sit amet, consectetuer adipiscing elit, sed diam nonummy nibh euismod tincidunt ut laoreet dolore magna aliquam erat volutpat. Ut wisi enim ad minim veniam, quis nostrud exerci tation ullamcorper suscipit lobortis nisl ut aliquip ex ea commodo consequat. Duis autem vel eum iriure dolor in hendrerit in vulputate velit esse molestie consequat.</p>
      <p class="body-copy" style="left:140px;top:150px;width:146px">Lorem ipsum dolor sit amet, consectetuer adipiscing elit, sed diam nonummy nibh euismod tincidunt ut laoreet dolore magna aliquam erat volutpat. Ut wisi enim ad minim veniam, quis nostrud exerci tation ullamcorper suscipit lobortis nisl ut aliquip ex ea commodo consequat. Duis autem vel eum iriure dolor in hendrerit in vulputate velit esse molestie consequat.</p>
      <div class="dates-head" style="left:140px;top:244px">Performance Dates</div>
      <ul class="dates" style="left:146px;top:260px">
        <li>Sept. 15 to Oct. 17, 2015</li><li>Théâtre des Lanternes du Nord</li>
        <li>Nov. 17 to 21, 2015</li><li>Harbourlight Repertory Theatre/Singapore</li>
        <li>Nov. 25 to 29, 2015</li><li>Kestrel Theatre/Tokyo/Japan</li>
        <li>Dec. 10 to 11, 2015</li><li>Maison des Arts d'Aubrac</li>
        <li>Feb. 3 to 27, 2016</li><li>Old Quay Theatre/London/Great Britain</li>
      </ul>
      <div class="footer-mark" style="left:14px">NEW PRODUCTION 2015/2016</div>
    </article>
  </section>

  <section class="cell">
    <article class="page detail-c">
      <div class="title" style="right:14px;top:18px">Act Name</div>
      <div class="subtitle" style="right:14px;top:46px">Based on the Act Name</div>
      <div class="topline"></div>
      <dl class="credits" style="left:14px;top:64px;width:124px;font-size:7px">
        <dt>Text By</dt><dd>Paul Brennan, Jean-Luc Corvalan and Marie-Claire Estoril</dd>
        <dt>Directed by</dt><dd>Paul Brennan &amp; Marie-Claire Estoril</dd>
        <dt>Music</dt><dd>Tomo Sakurai</dd>
        <dt>Lighting</dt><dd>Philippe Varenne</dd>
        <dt>With</dt><dd>Carine Kamanzi,<br>Jared Milburn, Eli Nzeyimana<br>and Sean O'Kearney</dd>
      </dl>
      <p class="body-copy" style="left:150px;top:66px;width:136px">Lorem ipsum dolor sit amet, consectetuer adipiscing elit, sed diam nonummy nibh euismod tincidunt ut laoreet dolore magna aliquam erat volutpat. Ut wisi enim ad minim veniam, quis nostrud exerci tation ullamcorper suscipit lobortis nisl ut aliquip ex ea commodo consequat. Duis autem vel eum iriure dolor in hendrerit in vulputate velit esse molestie consequat.</p>
      <div class="dates-head" style="left:150px;top:166px">Performance Dates</div>
      <ul class="dates" style="left:156px;top:182px">
        <li>Sept. 15 to Oct. 17, 2015</li><li>Théâtre des Lanternes du Nord</li>
        <li>Nov. 17 to 21, 2015</li><li>Harbourlight Repertory Theatre/Singapore</li>
      </ul>
      <div class="footer-mark" style="left:14px">NEW PRODUCTION 2015/2016</div>
    </article>
  </section>

</main>
</body>
</html>
```